Velk Partners Building Business Cards

We need a business card that reflects our business as "Solar Experts" in San Diego. Browse our website www.velkpartners.example our License needs to be displayed as "CSLB# 3867140" our phone number is (619) 555-0187

Save thousands on your electric bills and increase the value of your home while helping to protect the environment. Our solar installation experts will help you design the system that's right for you, using only the highest quality equipment that will look great and give you ideal performance. Our goal is to make you energy independent, and get your electric bill to 0.

Paul Osterby
(619) 555-0187
paul@velkpartners.example

Target Market(s)

Home owners in san diego looking for solar

Industry/Entity Type

Solar Energy

Contact Information for Business Card

Paul Osterby
(619) 555-0187
paul@velkpartners.example

Font styles to use
Other font styles liked:
• Use our logo font

Requirements
Must have
• License needs to be displayed as "CSLB# 3867140" our phone number is (619) 555-0187
Nice to have
• Real images of rooftop home solar in san diego
Should not have
• our business address

```html
<!DOCTYPE html>
<html lang="en">
<head>
<meta charset="utf-8">
<title>Velk Partners Building — Business Cards</title>
<link rel="stylesheet" href="https://fonts.googleapis.com/css2?family=Montserrat:wght@700;800&family=Open+Sans:wght@400;600&display=swap">
<style>
  :root {
    --navy: #1b3a72;
    --gold: #f5a800;
    --white: #ffffff;
    --ink: #3b3b3b;
    --bg: #e9eced;
    --rule: #e2e5e8;
  }
  * { box-sizing: border-box; margin: 0; padding: 0; }
  html, body { width: 1200px; height: 812px; overflow: hidden; }
  body {
    background: var(--bg);
    font-family: "Open Sans", Arial, sans-serif;
    position: relative;
  }
  .card {
    position: absolute;
    top: 258px;
    width: 520px;
    height: 297px;
    overflow: hidden;
    box-shadow: 0 6px 18px rgba(0,0,0,0.12);
  }
  .card-back { left: 50px; background: var(--navy); }
  .card-front { left: 630px; background: var(--white); }

  /* back side */
  .back-brand {
    position: absolute;
    top: 96px; left: 0; right: 0;
    display: flex; align-items: center; justify-content: center; gap: 14px;
  }
  .brand-dot {
    width: 34px; height: 34px; border-radius: 50%;
    background: var(--gold);
  }
  .back-brand .brand-name {
    font-family: "Montserrat", Arial, sans-serif;
    font-weight: 800; font-size: 26px; color: var(--white);
    letter-spacing: 0.2px;
  }
  .back-url {
    position: absolute; top: 214px; left: 0; right: 0;
    text-align: center; color: var(--white);
    font-size: 13px; letter-spacing: 2.5px;
  }

  /* front side */
  .front-brand {
    position: absolute; left: 26px; top: 118px;
    font-family: "Montserrat", Arial, sans-serif;
    font-weight: 800; font-size: 20px; color: var(--navy);
    line-height: 1.15; width: 200px;
  }
  .front-divider {
    position: absolute; left: 262px; top: 26px;
    width: 1px; height: 142px; background: var(--rule);
    box-shadow: -2px 0 6px rgba(0,0,0,0.06);
  }
  .contact { position: absolute; left: 282px; top: 26px; z-index: 1; }
  .contact-name {
    font-family: "Montserrat", Arial, sans-serif;
    font-weight: 800; font-size: 20px; color: var(--navy);
  }
  .contact-title { font-size: 14px; color: var(--gold); margin-top: 1px; }
  .contact-license { font-size: 13px; color: var(--ink); margin-top: 4px; }
  .contact-list { list-style: none; margin-top: 4px; }
  .contact-list li {
    display: flex; align-items: center; gap: 7px;
    font-size: 13px; color: var(--ink); line-height: 1.45;
  }
  .contact-list svg { width: 12px; height: 12px; flex: none; }
  .swoosh { position: absolute; left: 0; top: 0; }
</style>
</head>
<body>

  <section class="card card-back" aria-label="Business card, back">
    <div class="back-brand">
      <span class="brand-dot"></span>
      <span class="brand-name">Velk Partners Building</span>
    </div>
    <p class="back-url">WWW.VELKPARTNERS.EXAMPLE</p>
  </section>

  <section class="card card-front" aria-label="Business card, front">
    <div class="front-brand">Velk Partners Building</div>
    <div class="front-divider"></div>

    <div class="contact">
      <p class="contact-name">Paul Osterby</p>
      <p class="contact-title">CEO/Founder</p>
      <p class="contact-license">CSLB# 3867140</p>
      <ul class="contact-list">
        <li>
          <svg viewBox="0 0 24 24" fill="var(--navy)"><path d="M6.6 10.8a15.1 15.1 0 0 0 6.6 6.6l2.2-2.2a1 1 0 0 1 1-.25 11.4 11.4 0 0 0 3.6.57 1 1 0 0 1 1 1V20a1 1 0 0 1-1 1A17 17 0 0 1 3 4a1 1 0 0 1 1-1h3.5a1 1 0 0 1 1 1c0 1.25.2 2.45.57 3.57a1 1 0 0 1-.25 1z"/></svg>
          (619) 555-0187
        </li>
        <li>
          <svg viewBox="0 0 24 24" fill="var(--navy)"><path d="M2 5h20v14H2z"/><path d="M2 5l10 8 10-8" fill="none" stroke="#fff" stroke-width="2"/></svg>
          paul@velkpartners.example
        </li>
        <li>
          <svg viewBox="0 0 24 24"><circle cx="12" cy="12" r="10" fill="var(--navy)"/><path d="M2 12h20M12 2c3 3 3 17 0 20M12 2c-3 3-3 17 0 20" fill="none" stroke="#fff" stroke-width="1.4"/></svg>
          www.velkpartners.example
        </li>
      </ul>
    </div>

    <svg class="swoosh" width="520" height="297" viewBox="0 0 520 297" aria-hidden="true">
      <path d="M90 297 C290 286 450 246 520 176 L520 297 Z" fill="var(--gold)"/>
      <path d="M92 297 C292 290 452 254 520 190 L520 297 Z" fill="var(--white)"/>
      <path d="M120 297 C310 290 458 260 520 200 L520 297 Z" fill="var(--navy)"/>
    </svg>
  </section>

</body>
</html>
```